New Business Card Design Project

Need a design that will create an impact / strong impression towards our clients for our business. We are in the lighting business and we do lighting retrofits for large commercial to industrial clientele.

Target Market(s)

Lighting Industry

Industry/Entity Type

Business

Font styles to use
Other font styles liked:
• we would like to use the font on our logo, not sure what it is though..

Requirements
Must have
• Our logo.
Nice to have
• We are open to suggestions that have to do with lighting.

```html
<!DOCTYPE html>
<html lang="en">
<head>
<meta charset="utf-8">
<title>Brightline Retrofit Co. — Business Card</title>
<link rel="stylesheet" href="https://fonts.googleapis.com/css2?family=Lato:wght@400;700;900&display=swap">
<style>
  :root {
    --page-bg: #e8e9ea;
    --card-white: #ffffff;
    --brand-dark: #1f4a2a;
    --brand-green: #1e8a3c;
    --brand-light: #6cc04a;
    --text-grey: #6f6f6f;
    --back-top: #145a2d;
    --back-bottom: #0b3b1c;
    --back-text: #d8efd9;
  }
  * { box-sizing: border-box; margin: 0; padding: 0; }
  html, body {
    width: 1200px; height: 1000px; overflow: hidden;
    background: var(--page-bg);
    font-family: "Lato", Arial, sans-serif;
  }
  .canvas { position: relative; width: 1200px; height: 1000px; }

  .card {
    position: absolute; left: 240px; width: 696px; height: 396px;
    border-radius: 18px; overflow: hidden;
    box-shadow: 0 6px 14px rgba(0,0,0,0.18);
  }
  .card-front { top: 83px; background: var(--card-white); }
  .card-back {
    top: 520px;
    background: radial-gradient(ellipse at 50% 30%, var(--back-top) 0%, var(--back-bottom) 100%);
  }

  .brand-front {
    position: absolute; right: 32px; top: 52px;
    display: flex; align-items: center; gap: 10px;
  }
  .brand-front .brand-name {
    font-weight: 900; font-size: 26px; color: var(--brand-dark);
    letter-spacing: 0.5px;
  }
  .brand-mark { width: 14px; height: 14px; background: var(--brand-light); }

  .person { position: absolute; left: 30px; top: 193px; }
  .person-name {
    font-size: 21px; font-weight: 400; color: var(--brand-green);
    letter-spacing: 0.4px; text-transform: uppercase;
  }
  .person-title { font-size: 17px; color: var(--text-grey); margin-top: 2px; }

  .divider {
    position: absolute; left: 30px; right: 32px; top: 259px;
    height: 2px; background: var(--brand-light);
  }

  .contact-list {
    position: absolute; left: 30px; top: 275px; list-style: none;
  }
  .contact-list li {
    display: flex; align-items: center; gap: 14px;
    font-size: 15px; color: var(--text-grey); height: 22px;
    letter-spacing: 0.3px;
  }
  .contact-list svg { width: 14px; height: 14px; fill: var(--brand-green); }

  .address {
    position: absolute; right: 32px; top: 276px; text-align: right;
    font-size: 15px; line-height: 22px; color: var(--text-grey);
    letter-spacing: 0.3px;
  }

  .front-band { position: absolute; left: 0; bottom: 0; width: 696px; height: 30px; }

  .brand-back {
    position: absolute; left: 0; right: 0; top: 165px;
    display: flex; justify-content: center; align-items: center; gap: 14px;
  }
  .brand-back .brand-name {
    font-weight: 900; font-size: 38px; color: #ffffff; letter-spacing: 1px;
  }
  .brand-back .brand-mark { width: 20px; height: 20px; }

  .back-web {
    position: absolute; left: 0; right: 0; top: 354px; text-align: center;
    font-size: 14px; letter-spacing: 1.6px; color: var(--back-text);
  }
</style>
</head>
<body>
<main class="canvas">

  <section class="card card-front" aria-label="Business card front">
    <div class="brand-front">
      <span class="brand-name">BRIGHTLINE RETROFIT CO.</span>
      <span class="brand-mark"></span>
    </div>

    <div class="person">
      <p class="person-name">Daniel Reyes</p>
      <p class="person-title">Founder</p>
    </div>

    <div class="divider"></div>

    <ul class="contact-list">
      <li>
        <svg viewBox="0 0 24 24" aria-hidden="true"><path d="M6.6 10.8a15.1 15.1 0 0 0 6.6 6.6l2.2-2.2c.3-.3.7-.4 1-.2 1.1.4 2.3.6 3.6.6.6 0 1 .4 1 1V20c0 .6-.4 1-1 1A17 17 0 0 1 3 4c0-.6.4-1 1-1h3.5c.6 0 1 .4 1 1 0 1.3.2 2.5.6 3.6.1.3 0 .7-.2 1z"/></svg>
        0400 555 019
      </li>
      <li>
        <svg viewBox="0 0 24 24" aria-hidden="true"><path d="M2 5h20v14H2z" opacity="1"/><path d="M2 5l10 8 10-8" fill="none" stroke="#fff" stroke-width="2"/></svg>
        info@brightlineretro.com
      </li>
      <li>
        <svg viewBox="0 0 24 24" aria-hidden="true"><circle cx="12" cy="12" r="10"/><path d="M2 12h20M12 2c3 3 3 17 0 20M12 2c-3 3-3 17 0 20" fill="none" stroke="#fff" stroke-width="1.5"/></svg>
        www.brightlineretro.com
      </li>
    </ul>

    <p class="address">4810 Harbor Lane,<br>Suite Tempe 85281</p>

    <svg class="front-band" viewBox="0 0 696 30" aria-hidden="true">
      <rect x="0" y="5" width="410" height="6" fill="var(--brand-light)"/>
      <path d="M0 15 H395 C415 15 420 2 450 1 H696 V30 H0 Z" fill="var(--brand-green)"/>
    </svg>
  </section>

  <section class="card card-back" aria-label="Business card back">
    <div class="brand-back">
      <span class="brand-name">BRIGHTLINE RETROFIT CO.</span>
      <span class="brand-mark"></span>
    </div>
    <p class="back-web">www.brightlineretro.com</p>
  </section>

</main>
</body>
</html>
```